New design for www.TrimTable.com

On TrimTable you can find & book your hairdresser. TrimTable is the biggest platform in the Netherlands.

- The design should be a responcive design
- Should be able to go global, should fit in perfectly between all the big booking platforms like stayvo, ridlo etc,
- Should have te result of more bookings. :)
- We are ‘only’ asking a beautiful design, not a technical solution.
- We need a homepage (https://trimtable.com/), search resultpage ((https://trimtable.com/kapper/amsterdam/#), salonpage (https://trimtable.com/kapper/vorden/lumo-for-hair/), about us page (https://trimtable.com/aboutus/), for the hairdresser info page (https://trimtable.com/kapper/), login/register page (https://trimtable.com/account/signin/).

- On the page of the hairdresser there is a dynamic part. The part where you create your appointment. Please take a look at this part too after you choose your treatment (behandeling), employee (medewerker), Date (datum) and time (tijd). The part that you see after this, is the part where you fill in your data as a consumer.

I've added more logo's but mostly we use the green color.

A few of our competitors: www.plumsalo.com, www.korifex.com

Target Market(s)

All consumers

Industry/Entity Type

Hair And Beauty

Number of Pages Required

5+ page

Font styles to use
Sans Serif

Colors
abd036
c3c3c3
757575

Requirements
Must have
• Responsive
• We did an A/B test with the homepage. It turns out that option B works better then option A (take a look at the uploaded pictures). So what we need on the homepage: The USP's with the green checkboxes, The search button needs to by dynamic (changes for example from light green to dark green so you can see you can click it) The call to action sentence Zoek & Vind je kapsalon, the searchfield and searchbutton should be seperated.
Nice to have
• The style that we like is the flat design style. The website should be simple, clean and it should feel a bit like a luxury thing. Because an appointment with the hairdresser can be a real treat and luxury moment for yourself.
• The luxury feeling and flat design that is in the www.ridlo.com website is really nice for example. But then it has to be a bit more light and not so black and dark.

```html
<!DOCTYPE html>
<html lang="en">
<head>
<meta charset="utf-8">
<title>TrimTable – Find &amp; book your hairdresser</title>
<link rel="stylesheet" href="https://fonts.googleapis.com/css2?family=Open+Sans:wght@400;600;700;800&family=Roboto+Condensed:wght@700&display=swap">
<style>
  :root {
    --green: #8cc63f;
    --green-dark: #6fa52a;
    --orange: #f5921e;
    --orange-icon: #f0852a;
    --ink: #2b2b2b;
    --grey: #757575;
    --grey-light: #c3c3c3;
    --service-bg: #ececec;
    --panel: #ebe6d3;
    --white: #ffffff;
    --bar: #2d2d2d;
  }
  * { box-sizing: border-box; margin: 0; padding: 0; }
  html, body { width: 874px; height: 1200px; overflow: hidden; background: var(--white); }
  body { font-family: "Open Sans", Arial, sans-serif; color: var(--ink); }
  .page { position: relative; width: 874px; height: 1200px; overflow: hidden; }

  /* Hero */
  .hero { position: absolute; left: 0; top: 0; width: 874px; height: 435px; }
  .hero-photo { position: absolute; inset: 0;
    background: radial-gradient(ellipse at 45% 40%, #6b3a2c 0%, #3a1f1a 45%, #1c1112 100%); }
  .menu-toggle { position: absolute; right: 22px; top: 8px; width: 26px; height: 20px; background: var(--green); border-radius: 2px; }
  .menu-toggle span { position: absolute; left: 7px; width: 12px; height: 2px; background: var(--white); }
  .brand { position: absolute; top: 95px; left: 0; width: 100%; display: flex; justify-content: center; align-items: center; gap: 10px; }
  .brand-dot { width: 38px; height: 38px; border-radius: 50%; background: var(--white); }
  .brand-name { font-weight: 700; font-size: 34px; color: var(--white); letter-spacing: -0.5px; }
  .hero-title { position: absolute; top: 190px; width: 100%; text-align: center; font-family: "Roboto Condensed", Arial, sans-serif; font-weight: 700; font-size: 29px; color: var(--white); letter-spacing: 0.5px; }

  .search { position: absolute; left: 228px; top: 268px; width: 420px; }
  .search-tabs { display: flex; gap: 3px; }
  .search-tab { font-size: 8.5px; font-weight: 700; padding: 6px 10px; text-transform: uppercase; }
  .search-tab.is-active { background: var(--panel); color: var(--green-dark); }
  .search-tab.is-alt { background: var(--green); color: var(--white); }
  .search-panel { background: var(--panel); height: 84px; padding: 24px 22px; display: flex; }
  .search-input { flex: 1; height: 26px; background: var(--white); border: 1px solid var(--grey-light); font-size: 9px; color: var(--grey); padding: 7px 10px; }
  .search-button { width: 62px; height: 26px; margin-left: 6px; background: var(--green); color: var(--white); font-size: 9px; font-weight: 700; display: flex; align-items: center; justify-content: center; gap: 4px; }

  /* Services */
  .services { position: absolute; top: 435px; left: 0; width: 874px; height: 180px; background: var(--service-bg); display: flex; padding: 22px 50px 0; }
  .service { flex: 1; padding: 0 12px; }
  .service-icon { width: 40px; height: 40px; border-radius: 4px; background: var(--orange-icon); display: flex; align-items: center; justify-content: center; margin: 0 auto 12px; }
  .service-title { text-align: center; font-size: 10.5px; font-weight: 600; text-transform: uppercase; margin-bottom: 7px; }
  .service-text { text-align: center; font-size: 8.5px; line-height: 1.45; color: var(--grey); }

  /* About */
  .about { position: absolute; top: 615px; left: 0; width: 874px; height: 280px; }
  .about-visual { position: absolute; left: 18px; top: 30px; width: 312px; height: 225px; border-radius: 90px 110px 110px 20px;
    background: linear-gradient(120deg, #8a5a3c 0%, #c49a74 50%, #6e4a36 100%); }
  .about-mark { position: absolute; left: 438px; top: 35px; width: 30px; height: 30px; border-radius: 50%; background: var(--green); }
  .about-title { position: absolute; left: 478px; top: 28px; line-height: 1.05; }
  .about-title .lead { display: block; font-size: 25px; font-weight: 400; color: var(--ink); }
  .about-title .name { display: block; font-size: 29px; font-weight: 700; color: var(--green); }
  .about-rule { position: absolute; left: 440px; top: 112px; width: 420px; height: 16px; }
  .about-copy { position: absolute; left: 440px; top: 138px; width: 405px; font-size: 9.5px; line-height: 1.55; color: var(--ink); }
  .about-copy p + p { margin-top: 6px; }
  .cta { position: absolute; left: 440px; top: 240px; width: 112px; height: 28px; background: var(--green); color: var(--white); font-size: 10px; font-weight: 700; text-transform: uppercase; display: flex; align-items: center; justify-content: center; }

  /* Footer */
  .footer { position: absolute; top: 895px; left: 0; width: 874px; height: 270px; background: var(--orange); color: var(--white); }
  .footer-heading { font-size: 11px; font-weight: 700; text-transform: uppercase; margin-bottom: 12px; }
  .footer-heading .dark { color: var(--ink); }
  .col { position: absolute; top: 22px; }
  .links { left: 28px; list-style: none; }
  .links li { font-size: 9.5px; margin-bottom: 7px; padding-left: 12px; position: relative; }
  .links li::before { content: ""; position: absolute; left: 0; top: 5px; width: 4px; height: 4px; background: var(--white); }
  .contact { left: 170px; width: 170px; }
  .contact-row { display: flex; gap: 8px; font-size: 9px; line-height: 1.4; margin-bottom: 10px; }
  .contact-row svg { flex: none; margin-top: 1px; }
  .gallery { left: 355px; }
  .gallery-grid { display: grid; grid-template-columns: repeat(3, 32px); gap: 4px; }
  .gallery-thumb { width: 32px; height: 32px; background: linear-gradient(135deg, #6b4a3a, #b98b6a); }
  .gallery-more { margin-top: 8px; font-size: 9px; font-weight: 700; }
  .timings { left: 478px; width: 190px; }
  .timing-row { display: flex; background: var(--ink); margin-bottom: 4px; font-size: 9px; height: 22px; align-items: center; }
  .timing-day { width: 62px; padding-left: 8px; color: var(--green); font-weight: 700; }
  .timing-hours { color: var(--white); }
  .footer-brand { position: absolute; left: 500px; top: 218px; display: flex; align-items: center; gap: 8px; }
  .footer-brand .brand-dot { width: 26px; height: 26px; }
  .footer-brand .brand-name { font-size: 22px; }
  .app-visual { position: absolute; left: 690px; top: 14px; width: 110px; height: 256px; border-radius: 14px 14px 0 0;
    background: linear-gradient(180deg, #2a2a2a 0%, #3d3d3d 60%, #c98b63 100%); }

  .bottom-bar { position: absolute; top: 1165px; left: 0; width: 874px; height: 35px; background: var(--bar); display: flex; align-items: center; justify-content: space-between; padding: 0 26px; }
  .copyright { font-size: 8.5px; color: var(--grey-light); }
  .social { display: flex; gap: 6px; }
  .social span { width: 16px; height: 16px; border-radius: 50%; background: var(--grey); }
</style>
</head>
<body>
<div class="page">

  <header class="hero">
    <div class="hero-photo" role="img" aria-label="Hair salon interior with a stylist at work, warm dark tones"></div>
    <div class="menu-toggle"><span style="top:5px"></span><span style="top:9px"></span><span style="top:13px"></span></div>
    <div class="brand"><span class="brand-dot"></span><span class="brand-name">TrimTable</span></div>
    <h1 class="hero-title">THE GREATEST HAIR DRESSER BOOKING SITE</h1>

    <form class="search">
      <div class="search-tabs">
        <span class="search-tab is-active">Search Salon</span>
        <span class="search-tab is-alt">Book an Appointment</span>
      </div>
      <div class="search-panel">
        <div class="search-input">Salon name, Post code</div>
        <div class="search-button">
          <svg width="9" height="9" viewBox="0 0 10 10"><circle cx="4" cy="4" r="3" fill="none" stroke="#fff" stroke-width="1.5"/><line x1="6.3" y1="6.3" x2="9.3" y2="9.3" stroke="#fff" stroke-width="1.5"/></svg>
          SEARCH
        </div>
      </div>
    </form>
  </header>

  <section class="services">
    <div class="service">
      <div class="service-icon"><svg width="22" height="22" viewBox="0 0 22 22" fill="none" stroke="#fff" stroke-width="1.8"><circle cx="5" cy="16" r="3"/><circle cx="17" cy="16" r="3"/><line x1="7" y1="14" x2="17" y2="3"/><line x1="15" y1="14" x2="5" y2="3"/></svg></div>
      <div class="service-title">Cutting and Styling</div>
      <div class="service-text">Precise cuts shaped to suit your look.</div>
    </div>
    <div class="service">
      <div class="service-icon"><svg width="22" height="22" viewBox="0 0 22 22" fill="#fff"><rect x="9" y="2" width="4" height="8" rx="1"/><path d="M5 10h12l-2 10H7z"/></svg></div>
      <div class="service-title">Hair Color</div>
      <div class="service-text">Rich colour from subtle tones to bold.</div>
    </div>
    <div class="service">
      <div class="service-icon"><svg width="22" height="22" viewBox="0 0 22 22" fill="#fff"><path d="M11 2c4 6 6 9 6 12a6 6 0 0 1-12 0c0-3 2-6 6-12z"/></svg></div>
      <div class="service-title">Hair Treatment</div>
      <div class="service-text">Deep care that restores shine and strength.</div>
    </div>
    <div class="service">
      <div class="service-icon"><svg width="22" height="22" viewBox="0 0 22 22" fill="none" stroke="#fff" stroke-width="1.8"><path d="M4 6c0 9 4 13 7 13s7-4 7-13"/><line x1="8" y1="12" x2="14" y2="12"/></svg></div>
      <div class="service-title">Beard Treatment</div>
      <div class="service-text">Sharp beard trims and hot towel shaves.</div>
    </div>
    <div class="service">
      <div class="service-icon"><svg width="22" height="22" viewBox="0 0 22 22" fill="none" stroke="#fff" stroke-width="1.8"><rect x="5" y="3" width="12" height="7" rx="2"/><line x1="11" y1="10" x2="11" y2="20"/></svg></div>
      <div class="service-title">The Finish</div>
      <div class="service-text">Final styling so you leave feeling great.</div>
    </div>
  </section>

  <section class="about">
    <div class="about-visual" role="img" aria-label="Large initials filled with a photo of styled brown hair"></div>
    <span class="about-mark"></span>
    <h2 class="about-title"><span class="lead">WELCOME TO</span><span class="name">TRIMTABLE</span></h2>
    <svg class="about-rule" viewBox="0 0 420 16">
      <line x1="0" y1="8" x2="398" y2="8" stroke="#757575" stroke-width="1"/>
      <g fill="none" stroke="#2b2b2b" stroke-width="1.4"><circle cx="404" cy="4" r="2.5"/><circle cx="404" cy="12" r="2.5"/><line x1="406" y1="5.5" x2="418" y2="11"/><line x1="406" y1="10.5" x2="418" y2="5"/></g>
    </svg>
    <div class="about-copy">
      <p>Find the right salon near you, compare treatments and prices, read honest reviews and book your next appointment in a few clicks. Every visit to the hairdresser should feel like a small moment of luxury.</p>
      <p>Thousands of stylists and barbers trust us to fill their agenda. Choose your treatment, pick a stylist and a time that suits you, and we take care of the rest.</p>
    </div>
    <a class="cta">Get Started</a>
  </section>

  <footer class="footer">
    <div class="col" style="left:28px">
      <div class="footer-heading">Quick <span class="dark">Links</span></div>
      <ul class="links" style="position:static">
        <li>Home</li><li>About Us</li><li>Salon</li><li>Search</li><li>Result</li><li>Contact Us</li>
      </ul>
    </div>
    <div class="col contact">
      <div class="footer-heading">Contact <span class="dark">Details</span></div>
      <div class="contact-row"><svg width="9" height="11" viewBox="0 0 10 12"><path d="M5 0a4 4 0 0 1 4 4c0 3-4 8-4 8S1 7 1 4a4 4 0 0 1 4-4z" fill="#fff"/></svg><span>Lindengracht 42,<br>1015 KM Amsterdam</span></div>
      <div class="contact-row"><svg width="10" height="10" viewBox="0 0 10 10"><path d="M2 0l2 2-1 2a6 6 0 0 0 3 3l2-1 2 2-2 2C4 10 0 6 0 2z" fill="#fff"/></svg><span>+31 20 555 0142</span></div>
      <div class="contact-row"><svg width="10" height="8" viewBox="0 0 10 8"><rect width="10" height="8" fill="#fff"/><path d="M0 0l5 4 5-4" fill="none" stroke="#f5921e"/></svg><span>info@trimtable.com</span></div>
    </div>
    <div class="col gallery">
      <div class="footer-heading">Our <span class="dark">Gallery</span></div>
      <div class="gallery-grid" role="img" aria-label="Six small photos of salon haircuts">
        <span class="gallery-thumb"></span><span class="gallery-thumb"></span><span class="gallery-thumb"></span>
        <span class="gallery-thumb"></span><span class="gallery-thumb"></span><span class="gallery-thumb"></span>
      </div>
      <div class="gallery-more">VIEW ALL</div>
    </div>
    <div class="col timings">
      <div class="footer-heading">Office <span class="dark">Timings</span></div>
      <div class="timing-row"><span class="timing-day">MON - THUR</span><span class="timing-hours">9:00 AM - 7:00 PM</span></div>
      <div class="timing-row"><span class="timing-day">FRI &amp; SAT</span><span class="timing-hours">9:00 AM - 8:00 PM</span></div>
      <div class="timing-row"><span class="timing-day">SUN</span><span class="timing-hours">CLOSED</span></div>
    </div>
    <div class="footer-brand"><span class="brand-dot"></span><span class="brand-name">TrimTable</span></div>
    <div class="app-visual" role="img" aria-label="Hand holding a smartphone showing the booking app"></div>
  </footer>

  <div class="bottom-bar">
    <span class="copyright">Copyright 2015 TrimTable | All Rights Reserved</span>
    <div class="social"><span></span><span></span><span></span><span></span></div>
  </div>

</div>
</body>
</html>
```